Business Card design for law firm = Brightvale Australia

We are seeking a new design for our business cards.
We are keeping our logo, which is attached.
We need space for
Name
Title
Address is , which is
Level 7
214 Marlowe Street
Sydney NSW 2047
Phone :
Mobile :
Fax :
Email :
DX :
website www.brightvale-example.com.au

Industry/Entity Type

Law Firm / Banking and Finance

Contact Information for Business Card

We are seeking a new design for our business cards. We are keeping our logo. We need space for Name Title Address is Level 7 214 Marlowe Street Sydney NSW 2047 Phone Mobile Fax Email DX website www.brightvale-example.com.au

Colors
0054AA
0677BA
7BADD7
CADEEF
E8F1F8

Requirements
Must have
• see our website for general feel www.brightvale-example.com.au

```html
<!DOCTYPE html>
<html lang="en">
<head>
<meta charset="utf-8">
<title>Brightvale Australia — Business Card</title>
<link rel="stylesheet" href="https://fonts.googleapis.com/css2?family=EB+Garamond:wght@400&family=Source+Sans+3:wght@400&display=swap">
<style>
  :root {
    --backdrop: #b8b8b8;
    --paper: #ffffff;
    --brand-blue: #0077bb;
    --accent-blue: #00a3da;
    --ink-light: #ffffff;
    --shadow: rgba(0, 0, 0, 0.75);
  }
  * { box-sizing: border-box; margin: 0; padding: 0; }
  html, body { width: 1075px; height: 1200px; overflow: hidden; background: var(--backdrop); }
  .canvas { position: relative; width: 1075px; height: 1200px; }
  .card {
    position: absolute; left: 206px; width: 663px; height: 395px;
    box-shadow: 3px 3px 2px var(--shadow);
    overflow: hidden;
  }
  .card--front { top: 187px; background: var(--paper); }
  .card--back { top: 637px; background: var(--brand-blue); }

  .front__band {
    position: absolute; left: 0; top: 232px; width: 100%; height: 163px;
    background: var(--brand-blue);
  }
  .brand-name {
    position: absolute; font-family: "EB Garamond", Georgia, serif; font-weight: 400;
    line-height: 1; white-space: nowrap;
  }
  .card--front .brand-name { left: 387px; top: 126px; font-size: 44px; color: var(--brand-blue); }

  .person { position: absolute; left: 35px; top: 172px; }
  .person__name {
    font-family: "EB Garamond", Georgia, serif; font-size: 32px; line-height: 1;
    color: var(--brand-blue); white-space: nowrap;
  }
  .person__title {
    font-family: "Source Sans 3", Arial, sans-serif; font-size: 18px; line-height: 1;
    color: var(--accent-blue); margin-top: 2px;
  }
  .person__rule {
    position: absolute; left: 35px; top: 229px; width: 205px; height: 4px;
    background: var(--accent-blue);
  }

  .contacts {
    position: absolute; left: 36px; top: 254px; list-style: none;
    font-family: "Source Sans 3", Arial, sans-serif; font-size: 18.5px; color: var(--ink-light);
  }
  .contacts li { display: flex; align-items: center; height: 23.5px; white-space: nowrap; }
  .contacts svg { width: 19px; height: 19px; margin-right: 6px; flex: none; }

  .office {
    position: absolute; right: 39px; top: 284px; text-align: right; font-style: normal;
    font-family: "Source Sans 3", Arial, sans-serif; font-size: 18.5px; line-height: 24px;
    color: var(--ink-light);
  }
  .office__dx { margin-bottom: 10px; }

  .card--back .brand-name { left: 187px; top: 216px; font-size: 60px; color: var(--ink-light); }
</style>
</head>
<body>
<main class="canvas">
  <section class="card card--front" aria-label="Business card front">
    <div class="brand-name">Brightvale</div>

    <div class="person">
      <div class="person__name">Daniel Harper</div>
      <div class="person__title">Managing Director</div>
    </div>
    <div class="person__rule"></div>

    <div class="front__band"></div>

    <ul class="contacts">
      <li><svg viewBox="0 0 20 20" aria-hidden="true"><rect width="20" height="20" fill="#fff"/><path d="M5 4l3 0 1 3-2 1.5c1 2 2.5 3.5 4.5 4.5l1.5-2 3 1v3c-6 0-11-5-11-11z" fill="var(--brand-blue)"/></svg>044-555 010 234</li>
      <li><svg viewBox="0 0 20 20" aria-hidden="true"><rect width="20" height="20" fill="#fff"/><rect x="6" y="3" width="8" height="14" rx="1.5" fill="none" stroke="var(--brand-blue)" stroke-width="1.8"/><circle cx="10" cy="14.5" r="1" fill="var(--brand-blue)"/></svg>044-555 010 235</li>
      <li><svg viewBox="0 0 20 20" aria-hidden="true"><rect width="20" height="20" fill="#fff"/><rect x="6" y="3" width="8" height="4" fill="var(--brand-blue)"/><rect x="3" y="8" width="14" height="6" rx="1" fill="var(--brand-blue)"/><rect x="6" y="12" width="8" height="5" fill="#fff" stroke="var(--brand-blue)" stroke-width="1.5"/></svg>044-555 010 236</li>
      <li><svg viewBox="0 0 20 20" aria-hidden="true"><rect width="20" height="20" fill="#fff"/><rect x="3" y="5" width="14" height="10" fill="var(--brand-blue)"/><path d="M3 5l7 6 7-6" fill="none" stroke="#fff" stroke-width="1.3"/></svg>info@brightvale-example.com.au</li>
      <li><svg viewBox="0 0 20 20" aria-hidden="true"><rect width="20" height="20" fill="#fff"/><circle cx="10" cy="10" r="6" fill="none" stroke="var(--brand-blue)" stroke-width="1.4"/><ellipse cx="10" cy="10" rx="2.6" ry="6" fill="none" stroke="var(--brand-blue)" stroke-width="1.2"/><path d="M4 10h12M5 7h10M5 13h10" stroke="var(--brand-blue)" stroke-width="1"/></svg>www.brightvale-example.com.au</li>
    </ul>

    <address class="office">
      <div class="office__dx">DX :987650123</div>
      <div>Level 7, 214 Marlowe Street</div>
      <div>Sydney NSW 2047</div>
    </address>
  </section>

  <section class="card card--back" aria-label="Business card back">
    <div class="brand-name">Brightvale</div>
  </section>
</main>
</body>
</html>
```